Harbor Crestline (Business Card Design)

Need business cards designed. Something modern, chic, and sleek. Mabye the back of the card should be the navy blue that is in the logo and then just the logo on the back.

Target Market(s)

Those in the hotel, office, and renovation industry

Contact Information for Business Card

1. Logo 2. Dorian Fenwick 3. CEO/Founder 4. Phone: (833) HarbCre / (833) 427-2731 5. Email: dorian@theharborcrestline.com 6. Website: www.theharborcrestline.com

Font styles to use
Other font styles liked:
• Look at the logo font and base the font for everything else off of that.

Colors
0054AA
0677BA
7BADD7
CADEEF
E8F1F8

Requirements
Must have
• Colors that are associated in the logo
Nice to have
• Sleek modern clean and chic design.

```html
<!DOCTYPE html>
<html lang="en">
<head>
<meta charset="utf-8">
<title>Harbor Crestline — Business Card</title>
<link href="https://fonts.googleapis.com/css2?family=Montserrat:wght@500;600;700&family=Open+Sans:wght@400&display=swap" rel="stylesheet">
<style>
  :root {
    --navy: #0f1a42;
    --gold: #cda349;
    --white: #ffffff;
    --stage: #e4e6ea;
  }
  * { box-sizing: border-box; margin: 0; padding: 0; }
  html, body { width: 1200px; height: 947px; overflow: hidden; }
  body {
    background: var(--stage);
    display: flex;
    flex-direction: column;
    align-items: center;
    justify-content: center;
    gap: 56px;
    font-family: "Open Sans", sans-serif;
  }
  .card {
    position: relative;
    width: 560px;
    height: 320px;
    background: var(--navy);
    border-radius: 22px;
    overflow: hidden;
    box-shadow: 0 12px 30px rgba(15, 26, 66, 0.25);
  }
  .wordmark {
    display: flex;
    align-items: center;
    gap: 12px;
    font-family: "Montserrat", sans-serif;
    font-weight: 600;
    color: var(--white);
    text-transform: uppercase;
    letter-spacing: 0.12em;
    white-space: nowrap;
  }
  .wordmark__square { background: var(--gold); flex: none; }

  .card--front { display: flex; align-items: center; justify-content: center; }
  .card--front .wordmark { font-size: 34px; }
  .card--front .wordmark__square { width: 18px; height: 18px; }

  .name-tab {
    position: absolute;
    top: 30px; right: 0;
    width: 26px; height: 58px;
    background: var(--gold);
  }
  .identity {
    position: absolute;
    top: 32px; right: 44px;
    text-align: right;
  }
  .identity__name {
    font-family: "Montserrat", sans-serif;
    font-weight: 700;
    font-size: 26px;
    color: var(--gold);
    line-height: 1.1;
  }
  .identity__title {
    font-size: 15px;
    color: var(--white);
    margin-top: 4px;
  }
  .card--back .wordmark {
    position: absolute;
    left: 84px; top: 150px;
    font-size: 19px;
  }
  .card--back .wordmark__square { width: 11px; height: 11px; }
  .contacts {
    position: absolute;
    left: 0; bottom: 26px;
    list-style: none;
    display: flex;
    flex-direction: column;
    gap: 7px;
  }
  .contact { display: flex; align-items: center; gap: 16px; }
  .contact__icon {
    width: 66px; height: 28px;
    background: var(--gold);
    display: flex; align-items: center; justify-content: flex-end;
    padding-right: 10px;
  }
  .contact__icon svg { width: 15px; height: 15px; fill: var(--white); }
  .contact__text { font-size: 15px; color: var(--white); }
</style>
</head>
<body>
  <section class="card card--front" aria-label="Card front">
    <div class="wordmark">
      <span class="wordmark__square"></span>
      <span>Harbor Crestline</span>
    </div>
  </section>

  <section class="card card--back" aria-label="Card back">
    <span class="name-tab"></span>
    <div class="identity">
      <p class="identity__name">Dorian Fenwick</p>
      <p class="identity__title">Founder + CEO</p>
    </div>

    <div class="wordmark">
      <span class="wordmark__square"></span>
      <span>Harbor Crestline</span>
    </div>

    <ul class="contacts">
      <li class="contact">
        <span class="contact__icon">
          <svg viewBox="0 0 24 24" aria-hidden="true"><path d="M6.6 10.8a15.1 15.1 0 0 0 6.6 6.6l2.2-2.2a1 1 0 0 1 1-.25 11.4 11.4 0 0 0 3.6.57 1 1 0 0 1 1 1V20a1 1 0 0 1-1 1A17 17 0 0 1 3 4a1 1 0 0 1 1-1h3.5a1 1 0 0 1 1 1c0 1.25.2 2.45.57 3.57a1 1 0 0 1-.25 1z"/></svg>
        </span>
        <span class="contact__text">(833) 427-2731</span>
      </li>
      <li class="contact">
        <span class="contact__icon">
          <svg viewBox="0 0 24 24" aria-hidden="true"><path d="M3 5h18v14H3z M4.5 6.5 12 12l7.5-5.5" fill="none" stroke="#fff" stroke-width="2"/></svg>
        </span>
        <span class="contact__text">dorian@theharborcrestline.com</span>
      </li>
      <li class="contact">
        <span class="contact__icon">
          <svg viewBox="0 0 24 24" aria-hidden="true"><circle cx="12" cy="12" r="9" fill="none" stroke="#fff" stroke-width="2"/><path d="M3 12h18M12 3c3 3 3 15 0 18M12 3c-3 3-3 15 0 18" fill="none" stroke="#fff" stroke-width="1.6"/></svg>
        </span>
        <span class="contact__text">www.theharborcrestline.com</span>
      </li>
    </ul>
  </section>
</body>
</html>
```